Modern Business Card

Modern professional business card with more than just logo and demographic info. Something memorable.

We are a trendy/modern chiropractic group with an emphasis on neurology, hence the minimalist-type brain logo. We want to convey that modern and technical aspect with professionalism and the elite nature of our practice environment.

```html
<!DOCTYPE html>
<html lang="en">
<head>
<meta charset="utf-8">
<title>Keystone Spine – Business Card</title>
<link rel="stylesheet" href="https://fonts.googleapis.com/css2?family=Alegreya:wght@400&family=Arimo:wght@400&display=swap">
<style>
  :root {
    --page-bg: #e9e9ea;
    --brand-blue: #4680c4;
    --brand-black: #000000;
    --band-white: #ffffff;
    --band-grey: #ececec;
    --ink-dark: #1d1d1f;
    --ink-light: #ffffff;
    --icon-blue: #4a86cc;
  }
  html, body {
    margin: 0;
    width: 1200px;
    height: 900px;
    overflow: hidden;
    background: var(--page-bg);
  }
  .business-card {
    position: absolute;
    left: 150px;
    top: 171px;
    width: 900px;
    height: 557px;
    border-radius: 4px;
    overflow: hidden;
    box-shadow: 0 10px 30px rgba(0,0,0,0.18);
  }
  .card-shapes {
    position: absolute;
    inset: 0;
    display: block;
  }
  .brand-name {
    position: absolute;
    left: 98px;
    top: 240px;
    margin: 0;
    font-family: "Alegreya", Georgia, serif;
    font-weight: 400;
    color: var(--ink-dark);
    line-height: 1;
  }
  .brand-name .brand-line-main {
    display: block;
    font-size: 52px;
    letter-spacing: 1px;
  }
  .brand-name .brand-line-sub {
    display: block;
    font-size: 30px;
    letter-spacing: 7px;
    margin-top: 2px;
  }
  .holder {
    position: absolute;
    right: 64px;
    top: 50px;
    text-align: right;
    color: var(--ink-light);
  }
  .holder-name {
    margin: 0;
    font-family: "Alegreya", Georgia, serif;
    font-weight: 400;
    font-size: 33px;
    letter-spacing: 1.5px;
  }
  .holder-role {
    margin: 4px 0 0;
    font-family: "Arimo", Arial, sans-serif;
    font-size: 23px;
  }
  .address {
    position: absolute;
    right: 64px;
    top: 253px;
    margin: 0;
    text-align: right;
    font-family: "Arimo", Arial, sans-serif;
    font-style: normal;
    font-size: 25px;
    line-height: 34px;
    color: var(--ink-dark);
  }
  .contact-list {
    position: absolute;
    right: 64px;
    top: 404px;
    margin: 0;
    padding: 0;
    list-style: none;
    font-family: "Arimo", Arial, sans-serif;
    font-size: 25px;
    color: var(--ink-light);
  }
  .contact-list li {
    display: flex;
    justify-content: flex-end;
    align-items: center;
    gap: 8px;
    height: 35px;
  }
  .contact-icon {
    width: 24px;
    height: 24px;
    flex: none;
  }
</style>
</head>
<body>
  <article class="business-card">
    <svg class="card-shapes" viewBox="0 0 900 557" aria-hidden="true">
      <defs>
        <linearGradient id="bandShade" x1="0" y1="0" x2="0" y2="1">
          <stop offset="0" stop-color="var(--band-white)"/>
          <stop offset="1" stop-color="var(--band-grey)"/>
        </linearGradient>
        <radialGradient id="discShade" cx="0.45" cy="0.4" r="0.65">
          <stop offset="0" stop-color="#ffffff"/>
          <stop offset="1" stop-color="#e6e6e8"/>
        </radialGradient>
        <filter id="discShadow" x="-20%" y="-20%" width="140%" height="140%">
          <feDropShadow dx="0" dy="3" stdDeviation="5" flood-color="#000" flood-opacity="0.25"/>
        </filter>
      </defs>
      <rect class="base-black" width="900" height="557" fill="var(--brand-black)"/>
      <rect class="top-band" width="900" height="203" fill="var(--brand-blue)"/>
      <rect class="left-band" width="246" height="261" fill="var(--brand-blue)"/>
      <rect class="middle-band" x="246" y="203" width="654" height="150" fill="url(#bandShade)"/>
      <circle class="brand-disc" cx="246" cy="277" r="179" fill="url(#discShade)" filter="url(#discShadow)"/>
      <rect class="band-join" x="246" y="206" width="190" height="144" fill="url(#bandShade)" opacity="0"/>
    </svg>

    <h1 class="brand-name">
      <span class="brand-line-main">KEYSTONE</span>
      <span class="brand-line-sub">SPINE</span>
    </h1>

    <header class="holder">
      <h2 class="holder-name">MARCUS HALE</h2>
      <p class="holder-role">Managing Director</p>
    </header>

    <address class="address">
      18 Harbor Lane<br>
      Northbridge, 30418
    </address>

    <ul class="contact-list">
      <li>044-987 654 321
        <svg class="contact-icon" viewBox="0 0 24 24" aria-hidden="true">
          <rect x="1.5" y="1.5" width="21" height="21" rx="3" fill="none" stroke="var(--icon-blue)" stroke-width="2"/>
          <path d="M8 6.5c.6-.4 1.3-.3 1.6.3l1 2c.3.5.1 1.1-.3 1.4l-.7.5c.6 1.4 1.6 2.5 3 3.2l.5-.7c.3-.4.9-.6 1.4-.3l2 1c.6.3.7 1 .3 1.6l-.8 1c-.5.6-1.4.8-2.2.5-3.2-1.3-5.6-3.7-6.8-6.9-.3-.8-.1-1.6.5-2.1z" fill="var(--icon-blue)"/>
        </svg>
      </li>
      <li>hello@keystonespine.com
        <svg class="contact-icon" viewBox="0 0 24 24" aria-hidden="true">
          <rect x="1" y="5" width="22" height="15" rx="1" fill="var(--icon-blue)"/>
          <path d="M1.5 5.5 12 13.5 22.5 5.5" fill="none" stroke="#000" stroke-width="1.6"/>
        </svg>
      </li>
      <li>www.keystonespine.com
        <svg class="contact-icon" viewBox="0 0 24 24" aria-hidden="true">
          <g fill="none" stroke="var(--icon-blue)" stroke-width="1.8">
            <circle cx="12" cy="12" r="10"/>
            <ellipse cx="12" cy="12" rx="4.5" ry="10"/>
            <path d="M2 12h20M4 6.5h16M4 17.5h16"/>
          </g>
        </svg>
      </li>
    </ul>
  </article>
</body>
</html>
```